50th Anniversary Gala Save the date Postcard 8.5x5.5 inches

Looking for a 5.5x8.5 in one-sided postcard design for our annual gala. Design needs to include "Save the date" prominently with all the event information included below. Design should be light, include the colors of our logo and elegant. (almost like a wedding save the date). "Threads of Grace" should look like its own logo.

50th Anniversary Gala at The Lodge at Marrow Glen – “Threads of Grace – Celebrating 50 Years of Building Community”
Thursday, October 24
6-11p
The Lodge at Marrow Glen
Sallow Brook Road, New Hyde Park, NY
Honoring – TWR Previous Presidents

Target Market(s)

Exisiting donors

Industry/Entity Type

nonprofit

Font styles to use
Serif
Script

Requirements
Must have
• Save the date prominent
Should not have
• should not have a dark background

```html
<!DOCTYPE html>
<html lang="en">
<head>
<meta charset="utf-8">
<title>Save The Date – 50th Anniversary Gala</title>
<link rel="stylesheet" href="https://fonts.googleapis.com/css2?family=Great+Vibes&family=Roboto+Slab:wght@300;400;700&display=swap">
<style>
  :root {
    --page-bg: #eef1f2;
    --frame: #b9c5c9;
    --card: #ffffff;
    --ink: #1f1f1f;
    --royal: #1c3f9e;
    --sky: #3ea2dc;
    --azure: #2f74c0;
    --gold: #c9a12a;
    --gold-dark: #a8851d;
  }
  * { box-sizing: border-box; margin: 0; padding: 0; }
  html, body { width: 1200px; height: 938px; overflow: hidden; }
  body {
    background: var(--page-bg);
    display: flex; align-items: center; justify-content: center;
    font-family: "Roboto Slab", Georgia, serif;
    color: var(--ink);
  }
  .postcard {
    width: 1120px; height: 725px;
    background: var(--frame);
    padding: 26px;
    box-shadow: 0 6px 18px rgba(0,0,0,.12);
  }
  .postcard-face {
    width: 100%; height: 100%;
    background: radial-gradient(ellipse at 20% 30%, #f1f4f6 0%, var(--card) 55%);
    display: flex; flex-direction: column; align-items: center;
    padding-top: 46px; text-align: center;
  }
  .org-mark {
    display: flex; align-items: center; gap: 14px;
    font-weight: 700; font-size: 30px; color: var(--royal);
  }
  .org-mark-dot {
    width: 26px; height: 26px; border-radius: 50%; background: var(--gold);
  }
  .mark-rule {
    width: 250px; height: 2px; background: var(--gold); margin-top: 18px;
  }
  .save-date {
    font-family: "Great Vibes", cursive;
    font-size: 104px; line-height: 1; color: var(--sky);
    margin-top: 34px;
  }
  .gala-title { font-size: 29px; margin-top: 18px; }
  .theme-name {
    font-size: 30px; font-weight: 700; color: var(--royal);
    letter-spacing: 1px; margin-top: 6px;
  }
  .theme-tagline { font-size: 29px; margin-top: 6px; }
  .date-ribbon { position: relative; width: 560px; height: 58px; margin-top: 24px; }
  .date-ribbon svg { position: absolute; inset: 0; }
  .date-ribbon span {
    position: relative; display: block; line-height: 58px;
    color: #fff; font-weight: 700; font-size: 28px;
  }
  .venue { color: var(--sky); font-size: 26px; margin-top: 14px; }
  .address { color: var(--azure); font-weight: 300; font-size: 26px; margin-top: 4px; }
  .honoring { font-size: 20px; margin-top: 12px; }
</style>
</head>
<body>
  <main class="postcard">
    <section class="postcard-face">
      <div class="org-mark"><span class="org-mark-dot"></span>Thistle Way Resources</div>
      <div class="mark-rule"></div>

      <h1 class="save-date">Save The Date</h1>
      <p class="gala-title">50th Anniversary Gala at The Lodge at Marrow Glen</p>
      <p class="theme-name">THREADS OF GRACE</p>
      <p class="theme-tagline">Celebrating 50 Years of Building Community</p>

      <div class="date-ribbon">
        <svg viewBox="0 0 560 58" width="560" height="58" aria-hidden="true">
          <polygon points="0,6 30,29 0,52 40,52 40,6" fill="var(--gold-dark)"/>
          <polygon points="560,6 530,29 560,52 520,52 520,6" fill="var(--gold-dark)"/>
          <rect x="22" y="0" width="516" height="58" fill="var(--gold)"/>
        </svg>
        <span>THURSDAY, OCTOBER 24, 6-11P</span>
      </div>

      <p class="venue">The Lodge at Marrow Glen</p>
      <p class="address">Sallow Brook Road, New Hyde Park, NY</p>
      <p class="honoring">Honoring – TWR Previous Presidents</p>
    </section>
  </main>
</body>
</html>
```